Business Card Design Project

New Business Card design for Vantroke Technology Ltd using new Logo and new Tagline for staffing company.

About us from our website - www.vantroke-example.com:

VanTroke is a leading and recognized Electronic Entertainment, Workforce Augmentation, and Project Management solutions provider with clients in Electronic Entertainment, Legal, Technology, Government and other verticals that range in size from start up organizations to Meridex 500 companies. VanTroke is certified as an 8(a) minority and woman owned enterprise, established in 1998.

Target Market(s)

Companies in Electronic Entertainment, Legal, Government and Technology

Industry/Entity Type

Business

Requirements
Must have
• Must include in small letters the following information on back:

Established in 1998
8(a)(w)(e), Cage #7KTR9, DUNS #415260387

Front should have the following:
Pavel Orrin
Vice President
5678 Bramwick Lane
Tollerby, TB 654321
555-301-4826 X 100
555-309-1175 Fax
555-301-4826 Toll Free
name@vantroke-example.com

Our Tagline: Connect • Collaborate • Achieve

```html
<!DOCTYPE html>
<html lang="en">
<head>
<meta charset="utf-8">
<title>VanTroke Business Card</title>
<link href="https://fonts.googleapis.com/css2?family=Arimo:wght@400;700&display=swap" rel="stylesheet">
<style>
  :root {
    --backdrop: #cfcfd0;
    --card-dark: #3a3a3c;
    --card-dark-glow: #59595b;
    --card-light: #ffffff;
    --brand-blue: #0b5bb0;
    --brand-navy: #1b2f78;
    --ink: #1e1e1e;
    --logo-grey: #58595b;
    --on-dark: #ffffff;
  }
  * { box-sizing: border-box; margin: 0; padding: 0; }
  html, body { width: 1200px; height: 900px; overflow: hidden; }
  body {
    position: relative;
    background: var(--backdrop);
    font-family: "Arimo", Arial, sans-serif;
  }
  .card {
    position: absolute;
    width: 510px;
    height: 320px;
    border-radius: 18px;
    overflow: hidden;
    box-shadow: 0 4px 10px rgba(0,0,0,.25);
  }
  /* Back */
  .card-back {
    left: 190px; top: 115px;
    background: radial-gradient(ellipse at 50% 40%, var(--card-dark-glow) 0%, var(--card-dark) 70%);
    color: var(--on-dark);
  }
  .card-back .wordmark {
    position: absolute;
    top: 100px; left: 0; right: 0;
    text-align: center;
    font-weight: 700;
    font-size: 62px;
    letter-spacing: -1px;
    color: var(--on-dark);
  }
  .card-back .credentials {
    position: absolute;
    bottom: 28px; left: 0; right: 0;
    text-align: center;
    font-size: 14.5px;
    line-height: 22px;
  }
  /* Front */
  .card-front {
    left: 510px; top: 455px;
    background: var(--card-light);
    color: var(--ink);
  }
  .card-front .wordmark {
    position: absolute;
    top: 62px; left: 40px;
    font-weight: 700;
    font-size: 33px;
    letter-spacing: -0.5px;
    color: var(--logo-grey);
  }
  .card-front .tagline {
    position: absolute;
    top: 66px; left: 265px;
    font-size: 15px;
    color: var(--brand-blue);
  }
  .name-band {
    position: absolute;
    top: 162px; left: 0;
    width: 198px; height: 60px;
    padding: 14px 0 0 42px;
    background: linear-gradient(90deg, var(--brand-blue), var(--brand-navy));
    color: var(--on-dark);
  }
  .name-band .person { font-weight: 700; font-size: 17px; text-transform: uppercase; line-height: 20px; }
  .name-band .role { font-size: 14px; line-height: 18px; }
  .contact {
    position: absolute;
    top: 147px; left: 268px;
    list-style: none;
    font-size: 14.5px;
    line-height: 20.5px;
  }
  .contact li { display: flex; align-items: center; gap: 6px; }
  .contact svg { width: 13px; height: 13px; flex: none; }
  .contact .icon { fill: none; stroke: var(--brand-navy); stroke-width: 1.6; }
  .contact .icon-solid { fill: var(--brand-navy); }
</style>
</head>
<body>
  <section class="card card-back" aria-label="Card back">
    <div class="wordmark">VanTroke</div>
    <p class="credentials">Established in 1998<br>8(a)(w)(e), Cage #7KTR9, DUNS #415260387</p>
  </section>

  <section class="card card-front" aria-label="Card front">
    <div class="wordmark">VanTroke</div>
    <p class="tagline">Connect • Collaborate • Achieve</p>
    <div class="name-band">
      <div class="person">Pavel Orrin</div>
      <div class="role">Vice President</div>
    </div>
    <ul class="contact">
      <li>5678 Bramwick Lane</li>
      <li>Tollerby, TB 654321</li>
      <li><svg viewBox="0 0 14 14"><path class="icon-solid" d="M1 5c0-2 3-3 6-3s6 1 6 3l-3 1-1-2H5L4 6zM3 7h8l1 6H2z"/></svg>555-301-4826 x 100</li>
      <li><svg viewBox="0 0 14 14"><path class="icon-solid" d="M1 5c0-2 3-3 6-3s6 1 6 3l-3 1-1-2H5L4 6zM3 7h8l1 6H2z"/></svg>555-301-4826 Toll Free</li>
      <li><svg viewBox="0 0 14 14"><path class="icon" d="M4 6V1h6v5M2 6h10v6H2zM4 9h6"/></svg>555-309-1175</li>
      <li><svg viewBox="0 0 14 14"><path class="icon" d="M1 3h12v8H1zM1 3l6 5 6-5"/></svg>name@vantroke-example.com</li>
      <li><svg viewBox="0 0 14 14"><circle class="icon" cx="7" cy="7" r="5.5"/><path class="icon" d="M1.5 7h11M7 1.5c-3 3-3 8 0 11M7 1.5c3 3 3 8 0 11"/></svg>www.vantroke-example.com</li>
    </ul>
  </section>
</body>
</html>
```